Employee Benefits and Insurance Consulting

We are an existing company with over 30 years experience but are changing our name. We would like a simple design with grey tones.

Industry/Entity Type

Insurance

Contact Information for Business Card

Marlow Benefits Consulting
Gerald P Hollins CEO
5172 Brackenridge Road
Dunmore Falls, TN 37950
gerald@marlowbenefits-example.com
865-412-5593 - O
865-247-3861 - C

```html
<!DOCTYPE html>
<html lang="en">
<head>
<meta charset="utf-8">
<title>Marlow Benefits Consulting – Business Card</title>
<link rel="stylesheet" href="https://fonts.googleapis.com/css2?family=Open+Sans:wght@400;600;700;800&display=swap">
<style>
  :root {
    --backdrop: #d6d6d6;
    --card-black: #0a0a0a;
    --brand-red: #d11212;
    --swoosh-grey: #d9d9d9;
    --rule-grey: #6a6a6a;
    --text-white: #ffffff;
  }
  * { box-sizing: border-box; margin: 0; padding: 0; }
  html, body {
    width: 1200px;
    height: 900px;
    overflow: hidden;
    background: var(--backdrop);
    font-family: "Open Sans", Arial, sans-serif;
  }
  .canvas {
    width: 1200px;
    height: 900px;
    display: flex;
    flex-direction: column;
    align-items: center;
    justify-content: center;
    gap: 30px;
  }
  .card {
    position: relative;
    width: 720px;
    height: 411px;
    overflow: hidden;
    box-shadow: 0 4px 14px rgba(0,0,0,0.18);
  }

  /* Card back: brand side */
  .card-back {
    background: var(--card-black);
    display: flex;
    flex-direction: column;
    align-items: center;
    justify-content: center;
  }
  .brand-name {
    color: var(--brand-red);
    font-weight: 800;
    font-size: 38px;
    letter-spacing: 0.5px;
    line-height: 1.1;
  }
  .brand-rule {
    width: 470px;
    height: 1px;
    margin-top: 14px;
    background: var(--rule-grey);
  }

  /* Card front: contact side */
  .card-front { background: var(--brand-red); }
  .card-front .shape-layer {
    position: absolute;
    inset: 0;
    width: 100%;
    height: 100%;
  }
  .front-brand {
    position: absolute;
    left: 48px;
    top: 128px;
    color: var(--text-white);
    font-weight: 700;
    font-size: 34px;
    line-height: 1.15;
  }
  .contact-block {
    position: absolute;
    right: 22px;
    top: 78px;
    text-align: right;
    color: var(--text-white);
  }
  .person-name {
    font-weight: 700;
    font-size: 24px;
    margin-right: 26px;
  }
  .person-title {
    font-size: 15px;
    margin-right: 26px;
    margin-bottom: 26px;
  }
  .contact-line {
    display: flex;
    justify-content: flex-end;
    align-items: center;
    gap: 10px;
    font-size: 15px;
    line-height: 28px;
  }
  .contact-line svg { width: 16px; height: 16px; flex: none; }
  .address { margin-top: 22px; align-items: flex-end; }
  .address span { display: block; line-height: 24px; }
</style>
</head>
<body>
<main class="canvas">

  <section class="card card-back" aria-label="Business card back">
    <p class="brand-name">Marlow Benefits Consulting</p>
    <div class="brand-rule"></div>
  </section>

  <section class="card card-front" aria-label="Business card front">
    <svg class="shape-layer" viewBox="0 0 720 411" preserveAspectRatio="none" aria-hidden="true">
      <path d="M0 0 H358 C430 100 420 290 310 411 H0 Z" fill="var(--swoosh-grey)"/>
      <path d="M0 0 H340 C410 90 400 260 280 411 H0 Z" fill="var(--card-black)"/>
    </svg>

    <p class="front-brand">Marlow<br>Benefits<br>Consulting</p>

    <div class="contact-block">
      <p class="person-name">Gerald P Hollins</p>
      <p class="person-title">CEO</p>

      <p class="contact-line">865-247-3861
        <svg viewBox="0 0 24 24" aria-hidden="true"><path fill="#fff" d="M6.6 10.8a15.1 15.1 0 0 0 6.6 6.6l2.2-2.2c.3-.3.7-.4 1-.2 1.1.4 2.3.6 3.6.6.6 0 1 .4 1 1V20c0 .6-.4 1-1 1A17 17 0 0 1 3 4c0-.6.4-1 1-1h3.5c.6 0 1 .4 1 1 0 1.3.2 2.5.6 3.6.1.3 0 .7-.2 1z"/></svg>
      </p>
      <p class="contact-line">865-412-5593
        <svg viewBox="0 0 24 24" aria-hidden="true"><rect x="7" y="2" width="10" height="20" rx="2" fill="none" stroke="#fff" stroke-width="2"/><circle cx="12" cy="18" r="1.2" fill="#fff"/></svg>
      </p>
      <p class="contact-line">gerald@marlowbenefits-example.com
        <svg viewBox="0 0 24 24" aria-hidden="true"><rect x="2" y="5" width="20" height="14" rx="1" fill="#fff"/><path d="M2.5 5.5 12 13l9.5-7.5" fill="none" stroke="var(--brand-red)" stroke-width="1.6"/></svg>
      </p>

      <div class="contact-line address">
        <p><span>5172 Brackenridge Road</span><span>Dunmore Falls, TN 37950</span></p>
        <svg viewBox="0 0 24 24" aria-hidden="true"><path fill="#fff" d="M12 2a7 7 0 0 0-7 7c0 5.2 7 13 7 13s7-7.8 7-13a7 7 0 0 0-7-7zm0 9.5A2.5 2.5 0 1 1 12 6.5a2.5 2.5 0 0 1 0 5z"/></svg>
      </div>
    </div>
  </section>

</main>
</body>
</html>
```